Flyer für Immobilienmaklerunternehmen
Zielgruppe
Wir sind ein Immobilienmaklerunternehmen in Bochum.
Wir lassen die Flyer in die Briefkästen verteilen.
Wir möchten Eigentümer erreichen und diese am Besten zur Kontaktaufnahme motivieren. Oder zumindest in Erinnerung bleiben.
Viele brauchen unsere Dienstleistungen nur zu einem bestimmten Zeitpunkt.
Unsere Zielgruppe sind meist ältere Eigentümer, die entweder aus Sorge, wegen privatem Stress, Unwissenheit oder Erlösmaximierung einen Makler beauftragen.
Wir würden gerne mit den Flyern diejenigen ansprechen, die Sorge haben und ggf. unwissend sind. Hierbei stellen wir uns einen Flyer vor, der auf der Vorderseite ein Bild mit 'unsicheren Zeiten' nutzt, um Aufmerksamkeit zu erregen (wir haben bspw. einen Flyer mit einem Leuchtturm gesehen, der durch den Sturm den Weg weist, mit dem Spruch' Wir geben Ihnen auch in stürmischen Zeiten eine sichere Orientierung' etwas Ähnliches stellen wir uns vor) mit einem passenden Slogan.
Zudem hätten wir auf der Vorderseite ebenso unser Logo, als auch das Zertifikat.
Auf der Rückseite gerne die Motivation zur Kontaktaufnahme wie oben beschrieben, zudem hatten wir uns eine kurze Vorstellung unserer Dienstleistungen (Verkauf, Wertgutachten, Vermietung, Wohnflächenberechnung und Energieausweis) vorgestellt.
Dann hätten wir entweder gerne ein Teamfoto eingebaut mit Einladung zur Kontaktaufnahme, alternativ unseren Slogan 'Unser Erstgespräch kostet Sie einen Kaffee und einen Keks.' und anstelle des Teamfotos dann einem Bild von Kaffee und Keksen o.Ä.
Die Adressdaten der Firmen bitte sehr dezent/klein plazieren.
Bitte diese beiden Büros einbauen:
Kessling Immobilien
Wendelgasse 417
44879 Bochum
www.kessling-immobilien-beispiel.info
und
Tubel Immobilien
Lindmarkweg 27
44649 Herne
www.tubel-beispiel.de
(Bitte die Logos von der Homepage verwenden)
Aufgabenstellung
Unser Logo sollte zu finden sein, sowie die Geschäftsfarben (aus dem Logo)
Zudem muss die Handhabbarkeit beim Verteilen gegeben sein.
Wir kennen uns nicht so gut aus und benötigen am Schluss ein Ergebnis, mit dem wir die Flyer direkt drucken lassen können.
Bei Spezialformaten freuen wir uns, wenn Sie uns sagen, wo man diese drucken lassen kann.

```html
<!DOCTYPE html>
<html lang="de">
<head>
<meta charset="utf-8">
<title>Flyer Kessling Immobilien</title>
<link rel="stylesheet" href="https://fonts.googleapis.com/css2?family=Abril+Fatface&family=Caveat:wght@400&family=Jost:wght@400;500;600&family=Oswald:wght@400&family=Roboto+Slab:wght@700&display=swap">
<style>
  :root {
    --green: #7cb82f;
    --ink: #1d1d1b;
    --white: #ffffff;
    --paper: #ffffff;
    --forest-deep: #1b2418;
    --forest-mid: #4f6a35;
    --forest-teal: #2f5c63;
    --forest-light: #f1e6a6;
    --team-bg: #ececec;
    --team-dark: #222222;
    --badge: #1f2a5c;
  }
  * { box-sizing: border-box; margin: 0; padding: 0; }
  html, body { width: 1200px; height: 2400px; overflow: hidden; background: var(--paper); }
  body { position: relative; font-family: "Jost", sans-serif; color: var(--ink); }

  .panel {
    position: absolute; width: 510px; height: 1018px; background: var(--white);
    box-shadow: 4px 6px 10px rgba(0,0,0,.28); overflow: hidden;
  }
  .front-a { left: 67px; top: 96px; }
  .back-a { left: 625px; top: 94px; }
  .front-b { left: 64px; top: 1287px; width: 513px; }
  .back-b { left: 625px; top: 1287px; }

  /* brand mark */
  .brand {
    position: absolute; display: flex; align-items: center; gap: 10px;
    background: var(--white); padding: 10px 12px;
  }
  .brand-square { width: 16px; height: 16px; background: var(--green); flex: none; }
  .brand-name { font-family: "Jost", sans-serif; font-weight: 500; color: var(--ink); line-height: 1.05; letter-spacing: .04em; text-transform: uppercase; }

  /* front */
  .front-photo {
    position: absolute; left: 0; top: 92px; width: 100%; height: 864px;
    background:
      radial-gradient(ellipse 38% 30% at 42% 45%, var(--forest-light) 0%, rgba(226,214,140,.75) 35%, rgba(150,160,80,0) 80%),
      radial-gradient(ellipse 60% 40% at 90% 10%, rgba(70,130,140,.85) 0%, rgba(47,92,99,0) 70%),
      linear-gradient(90deg, rgba(20,30,20,.55) 0%, rgba(20,30,20,0) 25%, rgba(20,30,20,0) 75%, rgba(20,40,40,.5) 100%),
      linear-gradient(180deg, var(--forest-teal) 0%, #6f7f45 30%, #8a8f4c 50%, #4b5c2c 70%, var(--forest-deep) 88%, #141a12 100%);
  }
  .front .brand { left: 34px; top: 23px; width: 146px; height: 112px; border: 3px solid var(--green); }
  .front .brand-name { font-size: 17px; }
  .headline, .claim-big {
    position: absolute; left: 0; width: 100%; text-align: center;
    font-family: "Abril Fatface", serif; line-height: 1; font-weight: 400;
  }
  .headline { top: 188px; font-size: 54px; }
  .claim-big.one { top: 770px; font-size: 44px; }
  .claim-big.two { top: 843px; font-size: 48px; }
  .claim-script {
    position: absolute; left: 0; width: 100%; text-align: center;
    font-family: "Caveat", cursive; font-size: 27px; line-height: 1;
  }
  .claim-script.one { top: 815px; }
  .claim-script.two { top: 897px; }
  .front-a .headline, .front-a .claim-big { color: var(--green); }
  .front-a .claim-script { color: var(--white); }
  .front-b .headline, .front-b .claim-big { color: var(--white); }
  .front-b .claim-script { color: var(--green); }

  .footer-bar {
    position: absolute; left: 0; bottom: 0; width: 100%; height: 62px;
    background: var(--green); color: var(--white);
    display: flex; align-items: center; justify-content: center;
  }
  .front .footer-bar { font-size: 26px; }
  .back .footer-bar { font-size: 15.5px; letter-spacing: -.01em; }

  /* back */
  .services-title {
    position: absolute; left: 55px; top: 88px;
    font-family: "Roboto Slab", serif; font-weight: 700; color: var(--green);
    font-size: 30px; line-height: 37px;
  }
  .back .brand { left: 317px; top: 33px; width: 140px; height: 116px; border: 3px solid var(--green); }
  .back .brand-name { font-size: 17px; }
  .services { position: absolute; left: 55px; top: 173px; list-style: none; }
  .services li { display: flex; align-items: center; height: 41px; font-size: 27px; }
  .services svg { width: 22px; height: 22px; margin-right: 28px; flex: none; }
  .cta { position: absolute; left: 0; top: 405px; width: 100%; height: 80px; }
  .cta-text {
    position: absolute; left: 100px; top: 0;
    font-family: "Oswald", sans-serif; color: var(--green); font-size: 27px; line-height: 35px;
    transform: scaleX(.84); transform-origin: left top; white-space: nowrap;
  }
  .cta svg { position: absolute; top: 22px; width: 26px; height: 42px; }
  .cta .chev-left { left: 55px; }
  .cta .chev-right { left: 434px; }

  .team-photo {
    position: absolute; left: 0; top: 511px; width: 100%; height: 267px;
    background:
      radial-gradient(ellipse 14% 22% at 12% 30%, rgba(214,190,140,.8) 0%, rgba(214,190,140,0) 100%),
      radial-gradient(ellipse 14% 22% at 31% 28%, rgba(222,200,150,.8) 0%, rgba(222,200,150,0) 100%),
      radial-gradient(ellipse 14% 22% at 50% 22%, rgba(190,160,130,.7) 0%, rgba(190,160,130,0) 100%),
      radial-gradient(ellipse 14% 22% at 71% 38%, rgba(200,175,140,.7) 0%, rgba(200,175,140,0) 100%),
      radial-gradient(ellipse 14% 22% at 91% 18%, rgba(190,160,130,.7) 0%, rgba(190,160,130,0) 100%),
      linear-gradient(180deg, var(--team-bg) 0%, #e4e4e4 40%, #8a8a8a 62%, var(--team-dark) 100%);
  }
  .offices { position: absolute; left: 0; top: 778px; width: 100%; height: 178px; }
  .offices .divider { position: absolute; left: 262px; top: 2px; width: 1px; height: 160px; background: #555; }
  .office { position: absolute; top: 12px; }
  .office.home { left: 53px; width: 200px; }
  .office.partner { left: 288px; }
  .office-mark { display: flex; align-items: center; gap: 6px; height: 62px; }
  .office-mark .brand-square { width: 11px; height: 11px; }
  .office-mark .brand-name { font-size: 12px; }
  .partner-badge { width: 38px; height: 38px; background: var(--badge); margin-left: 6px; }
  .office address { font-style: normal; font-size: 13px; line-height: 16.5px; margin-top: 4px; white-space: nowrap; }
  .office .phone { font-weight: 600; }
  .office .web { font-size: 11px; letter-spacing: -.01em; }
  .office.home .web { font-size: 10.3px; }
</style>
</head>
<body>

<section class="panel front front-a">
  <div class="front-photo" role="img" aria-label="Nebliger Wald mit Sonnenlicht zwischen den Bäumen"></div>
  <div class="brand"><span class="brand-square"></span><span class="brand-name">Kessling<br>Immobilien</span></div>
  <h1 class="headline">Lauter Bäume?</h1>
  <p class="claim-big one">Wir helfen Ihnen</p>
  <p class="claim-script one">auch in den unsicheren Zeiten</p>
  <p class="claim-big two">den Wald zu sehen</p>
  <p class="claim-script two">...und bringen Licht in's Dunkel.</p>
  <div class="footer-bar">Ihr Immobilienmarkler aus Bochum.</div>
</section>

<section class="panel back back-a">
  <h2 class="services-title">Unsere<br>Dienstleistungen:</h2>
  <div class="brand"><span class="brand-square"></span><span class="brand-name">Kessling<br>Immobilien</span></div>
  <ul class="services">
    <li><svg viewBox="0 0 22 22"><rect x="1" y="3" width="18" height="18" fill="none" stroke="#7cb82f" stroke-width="2"/><path d="M5 12l4 4 11-14" fill="none" stroke="#7cb82f" stroke-width="2.4"/></svg>Verkauf</li>
    <li><svg viewBox="0 0 22 22"><rect x="1" y="3" width="18" height="18" fill="none" stroke="#7cb82f" stroke-width="2"/><path d="M5 12l4 4 11-14" fill="none" stroke="#7cb82f" stroke-width="2.4"/></svg>Wertgutachten</li>
    <li><svg viewBox="0 0 22 22"><rect x="1" y="3" width="18" height="18" fill="none" stroke="#7cb82f" stroke-width="2"/><path d="M5 12l4 4 11-14" fill="none" stroke="#7cb82f" stroke-width="2.4"/></svg>Vermietung</li>
    <li><svg viewBox="0 0 22 22"><rect x="1" y="3" width="18" height="18" fill="none" stroke="#7cb82f" stroke-width="2"/><path d="M5 12l4 4 11-14" fill="none" stroke="#7cb82f" stroke-width="2.4"/></svg>Wohnflächenberechnung</li>
    <li><svg viewBox="0 0 22 22"><rect x="1" y="3" width="18" height="18" fill="none" stroke="#7cb82f" stroke-width="2"/><path d="M5 12l4 4 11-14" fill="none" stroke="#7cb82f" stroke-width="2.4"/></svg>Energieausweis</li>
  </ul>
  <div class="cta">
    <svg class="chev-left" viewBox="0 0 26 42"><path d="M4 2l18 19L4 40" fill="none" stroke="#7cb82f" stroke-width="7"/></svg>
    <p class="cta-text">Rufen Sie uns an und vereinbaren<br>ein unverbindliches Erstgespräch.</p>
    <svg class="chev-right" viewBox="0 0 26 42"><path d="M22 2L4 21l18 19" fill="none" stroke="#7cb82f" stroke-width="7"/></svg>
  </div>
  <div class="team-photo" role="img" aria-label="Teamfoto mit fünf Mitarbeitenden vor hellem Hintergrund"></div>
  <div class="offices">
    <div class="office home">
      <div class="office-mark"><span class="brand-square"></span><span class="brand-name">Kessling Immobilien</span></div>
      <address>Kessling Immobilien<br>Wendelgasse 417<br>44879 Bochum<br><span class="phone">0234 / 55501234</span><br><span class="web">www.kessling-immobilien-beispiel.info</span></address>
    </div>
    <span class="divider"></span>
    <div class="office partner">
      <div class="office-mark"><span class="brand-name">Tubel Immobilien</span><span class="partner-badge"></span></div>
      <address>Tubel Immobilien<br>Lindmarkweg 27<br>44649 Herne<br>02325 / 55509<br><span class="web">www.tubel-beispiel.de</span></address>
    </div>
  </div>
  <div class="footer-bar">Unser Erstgespräch kostet Sie nur einen Kaffee und leckere Kekse</div>
</section>

<section class="panel front front-b">
  <div class="front-photo" role="img" aria-label="Nebliger Wald mit Sonnenlicht zwischen den Bäumen"></div>
  <div class="brand"><span class="brand-square"></span><span class="brand-name">Kessling<br>Immobilien</span></div>
  <h1 class="headline">Lauter Bäume?</h1>
  <p class="claim-big one">Wir helfen Ihnen</p>
  <p class="claim-script one">auch in den unsicheren Zeiten</p>
  <p class="claim-big two">den Wald zu sehen</p>
  <p class="claim-script two">...und bringen Licht in's Dunkel.</p>
  <div class="footer-bar">Ihr Immobilienmarkler aus Bochum.</div>
</section>

<section class="panel back back-b">
  <h2 class="services-title">Unsere<br>Dienstleistungen:</h2>
  <div class="brand"><span class="brand-square"></span><span class="brand-name">Kessling<br>Immobilien</span></div>
  <ul class="services">
    <li><svg viewBox="0 0 22 22"><rect x="1" y="3" width="18" height="18" fill="none" stroke="#7cb82f" stroke-width="2"/><path d="M5 12l4 4 11-14" fill="none" stroke="#7cb82f" stroke-width="2.4"/></svg>Verkauf</li>
    <li><svg viewBox="0 0 22 22"><rect x="1" y="3" width="18" height="18" fill="none" stroke="#7cb82f" stroke-width="2"/><path d="M5 12l4 4 11-14" fill="none" stroke="#7cb82f" stroke-width="2.4"/></svg>Wertgutachten</li>
    <li><svg viewBox="0 0 22 22"><rect x="1" y="3" width="18" height="18" fill="none" stroke="#7cb82f" stroke-width="2"/><path d="M5 12l4 4 11-14" fill="none" stroke="#7cb82f" stroke-width="2.4"/></svg>Vermietung</li>
    <li><svg viewBox="0 0 22 22"><rect x="1" y="3" width="18" height="18" fill="none" stroke="#7cb82f" stroke-width="2"/><path d="M5 12l4 4 11-14" fill="none" stroke="#7cb82f" stroke-width="2.4"/></svg>Wohnflächenberechnung</li>
    <li><svg viewBox="0 0 22 22"><rect x="1" y="3" width="18" height="18" fill="none" stroke="#7cb82f" stroke-width="2"/><path d="M5 12l4 4 11-14" fill="none" stroke="#7cb82f" stroke-width="2.4"/></svg>Energieausweis</li>
  </ul>
  <div class="cta">
    <svg class="chev-left" viewBox="0 0 26 42"><path d="M4 2l18 19L4 40" fill="none" stroke="#7cb82f" stroke-width="7"/></svg>
    <p class="cta-text">Rufen Sie uns an und vereinbaren<br>ein unverbindliches Erstgespräch.</p>
    <svg class="chev-right" viewBox="0 0 26 42"><path d="M22 2L4 21l18 19" fill="none" stroke="#7cb82f" stroke-width="7"/></svg>
  </div>
  <div class="team-photo" role="img" aria-label="Teamfoto mit fünf Mitarbeitenden vor hellem Hintergrund"></div>
  <div class="offices">
    <div class="office home">
      <div class="office-mark"><span class="brand-square"></span><span class="brand-name">Kessling Immobilien</span></div>
      <address>Kessling Immobilien<br>Wendelgasse 417<br>44879 Bochum<br><span class="phone">0234 / 55501234</span><br><span class="web">www.kessling-immobilien-beispiel.info</span></address>
    </div>
    <span class="divider"></span>
    <div class="office partner">
      <div class="office-mark"><span class="brand-name">Tubel Immobilien</span><span class="partner-badge"></span></div>
      <address>Tubel Immobilien<br>Lindmarkweg 27<br>44649 Herne<br>02325 / 55509<br><span class="web">www.tubel-beispiel.de</span></address>
    </div>
  </div>
  <div class="footer-bar">Unser Erstgespräch kostet Sie nur einen Kaffee und leckere Kekse</div>
</section>

</body>
</html>
```